Maple Grove Schools | brand new stationery!

We need stationery design with our new logo! Our company updated it's name and image and we like to incorporate the new one on our stationery, business cards and email signature. We are looking for fresh, new ideas!
Industry: Childcare, Elementary and Middle School
Company Name: Maple Grove Schools
Tagline: Bright Futures Start Here
Main colors: Blue, white and a little yellow
Star shape is something new for us! Do you see a way to incorporate it as a design element?

```html
<!DOCTYPE html>
<html lang="en">
<head>
<meta charset="utf-8">
<title>Maple Grove Schools – Business Card</title>
<link rel="stylesheet" href="https://fonts.googleapis.com/css2?family=Sora:wght@400;600&family=Poppins:wght@600&family=Arimo&family=Playfair+Display&display=swap">
<style>
  :root {
    --backdrop: #212121;
    --navy: #041a6e;
    --yellow: #f7bf1a;
    --white: #ffffff;
    --ink: #1e1b1c;
  }
  * { margin: 0; padding: 0; box-sizing: border-box; }
  html, body { width: 1075px; height: 1200px; overflow: hidden; background: var(--backdrop); }
  .stage { position: relative; width: 1075px; height: 1200px; }
  .card {
    position: absolute; width: 664px; height: 395px; background: var(--white);
    box-shadow: 3px 3px 4px rgba(0,0,0,.6); overflow: hidden;
  }
  .card--front { left: 206px; top: 187px; }
  .card--back { left: 203px; top: 637px; }
  .card__shape { position: absolute; inset: 0; width: 100%; height: 100%; }
  .brand { position: absolute; text-align: center; color: var(--ink);
    font-family: "Sora", sans-serif; font-weight: 600; line-height: 1.1; letter-spacing: -0.5px; }
  .brand__sub { display: block; font-weight: 400; letter-spacing: 0; }
  .brand__mark { display: block; margin: 0 auto; border-radius: 50%; background: var(--navy); }
  .card--front .brand { left: 19px; width: 300px; top: 62px; font-size: 40px; }
  .card--front .brand__mark { width: 66px; height: 66px; margin-bottom: 22px; }
  .card--back .brand { left: 132px; width: 400px; top: 68px; font-size: 56px; }
  .card--back .brand__mark { width: 104px; height: 104px; margin-bottom: 26px; }
  .contact { position: absolute; right: 42px; top: 196px; text-align: right;
    color: var(--white); font-family: "Arimo", sans-serif; font-size: 17px; line-height: 23.5px; }
  .contact__name { font-family: "Poppins", sans-serif; font-weight: 600; color: var(--yellow);
    font-size: 24px; line-height: 28px; }
  .contact__role { margin-bottom: 10px; }
  .contact__line { display: flex; justify-content: flex-end; align-items: center; gap: 5px; }
  .contact__line svg { width: 16px; height: 16px; flex: none; }
  .contact__address { margin-top: 10px; }
  .tagline { position: absolute; right: 26px; top: 258px; text-align: right; color: var(--yellow);
    font-family: "Playfair Display", serif; font-size: 31px; line-height: 35px; }
</style>
</head>
<body>
<main class="stage">
  <section class="card card--front">
    <svg class="card__shape" viewBox="0 0 739 439" preserveAspectRatio="none" aria-hidden="true">
      <path d="M80 439 C250 400 420 260 590 0 L739 0 L739 439 Z" fill="var(--navy)"/>
      <path d="M0 439 C190 432 360 310 500 132" fill="none" stroke="var(--yellow)" stroke-width="5"/>
    </svg>
    <div class="brand"><span class="brand__mark"></span>Maple Grove<span class="brand__sub">Schools</span></div>
    <div class="contact">
      <div class="contact__name">Daniel Harper</div>
      <div class="contact__role">Managing Director</div>
      <div class="contact__line">044-987 654 321
        <svg viewBox="0 0 16 16"><path d="M4 1.5 6.5 5 5 6.5c.8 1.8 2.3 3.3 4.5 4.5L11 9.5l3.5 2.5-1.5 2.5C7.5 14 2 8.5 1.5 3z" fill="var(--yellow)"/></svg></div>
      <div class="contact__line">hello@maplegrove.org
        <svg viewBox="0 0 16 16"><rect x="1" y="3" width="14" height="10" fill="var(--yellow)"/><path d="M1 3 8 9l7-6" fill="none" stroke="var(--navy)" stroke-width="1.3"/></svg></div>
      <div class="contact__line">www.maplegrove.org
        <svg viewBox="0 0 16 16" fill="none" stroke="var(--yellow)" stroke-width="1.4"><circle cx="8" cy="8" r="6.5"/><ellipse cx="8" cy="8" rx="3" ry="6.5"/><path d="M1.5 8h13M2.5 5h11M2.5 11h11"/></svg></div>
      <div class="contact__address">18, Willow Lane Northfield<br>60318, Eastland</div>
    </div>
  </section>

  <section class="card card--back">
    <svg class="card__shape" viewBox="0 0 738 439" preserveAspectRatio="none" aria-hidden="true">
      <path d="M385 439 C520 380 640 230 738 98 L738 439 Z" fill="var(--navy)"/>
      <path d="M368 439 C470 402 560 322 628 240" fill="none" stroke="var(--yellow)" stroke-width="4"/>
    </svg>
    <div class="brand"><span class="brand__mark"></span>Maple Grove<span class="brand__sub">Schools</span></div>
    <p class="tagline">Bright<br>Futures<br>Start Here!</p>
  </section>
</main>
</body>
</html>
```